Meridale Nutrition needs Stationary and a business card

We would like to use our current logo. The text can be moved around as needed. The stationary needs to be a 'first page' where the logo is more prominent to be impressive on higher quality paper and a second page where the logo is more subtle where there will be much more information on the page. There are 2 clinic locations which will need include name, address, phone number, fax number, web address. The business card should be single sided and contain this information also.
The design must be contemporary and sophisticated as this is a science based diet run out of a medical clinic.

Target Market(s)

People wanting to lose weight, athletes looking to optimise performance, people with arthritis or fighting cancer

Industry/Entity Type

Business

Contact Information for Business Card

must use the logo. I have attached an example card with the practice details on it. there must be space for the doctors name. Also the website www.meridalenutrition.com.au

Requirements
Must have
• the logo, the business adresses and phone numbers, the website, the doctors name and qualifications
Nice to have
• some creativity
Should not have
• Do not simply reproduce the existing card please

```html
<!DOCTYPE html>
<html lang="en">
<head>
<meta charset="utf-8">
<title>Meridale Nutrition – Business Card</title>
<link href="https://fonts.googleapis.com/css2?family=Questrial&display=swap" rel="stylesheet">
<style>
  :root {
    --page-bg: #e9e6e2;
    --frost-light: #f4f6f8;
    --frost-mid: #e3e9ee;
    --teal-dark: #17819a;
    --teal-mid: #1f98b6;
    --teal-bright: #2fa9dc;
    --ink-navy: #2a4766;
    --ink-soft: #d8eef6;
    --brand-blue: #3a6f97;
    --divider: #2c4a66;
  }
  html, body {
    margin: 0;
    padding: 0;
    width: 1200px;
    height: 970px;
    overflow: hidden;
    background: var(--page-bg);
    font-family: "Questrial", sans-serif;
  }
  .business-card {
    position: absolute;
    left: 100px;
    top: 200px;
    width: 1000px;
    height: 567px;
    display: flex;
    box-shadow: 0 14px 40px rgba(0,0,0,0.18);
  }
  .card-front {
    position: relative;
    width: 490px;
    height: 100%;
    background: linear-gradient(160deg, var(--frost-light) 0%, var(--frost-mid) 70%, #eadfe0 100%);
  }
  .card-divider {
    width: 6px;
    height: 100%;
    background: var(--divider);
  }
  .card-details {
    position: relative;
    flex: 1;
    height: 100%;
    background: linear-gradient(100deg, var(--teal-dark) 0%, var(--teal-mid) 55%, var(--teal-bright) 100%);
  }
  .brand-mark {
    position: absolute;
    left: 145px;
    top: 140px;
    width: 200px;
    height: 200px;
    border-radius: 50%;
    background: var(--brand-blue);
  }
  .brand-name {
    position: absolute;
    left: 0;
    width: 490px;
    top: 362px;
    text-align: center;
    font-size: 38px;
    color: var(--brand-blue);
    letter-spacing: 0.5px;
  }
  .details-inner {
    position: absolute;
    left: 60px;
    top: 52px;
    right: 30px;
  }
  .person-name {
    margin: 0;
    font-size: 40px;
    line-height: 46px;
    font-weight: 400;
    color: var(--ink-navy);
  }
  .person-title {
    margin: 2px 0 0;
    font-size: 22px;
    line-height: 28px;
    color: var(--ink-soft);
  }
  .clinic {
    margin-top: 22px;
  }
  .clinic-name {
    margin: 0;
    font-size: 19px;
    line-height: 26px;
    color: var(--ink-navy);
    letter-spacing: 0.5px;
  }
  .clinic-address {
    margin: 0;
    font-size: 19px;
    line-height: 26px;
    font-style: normal;
    color: var(--ink-soft);
  }
  .clinic-lines {
    display: flex;
    gap: 26px;
    margin-top: 4px;
  }
  .contact-item {
    display: flex;
    align-items: center;
    height: 30px;
    font-size: 19px;
    color: var(--ink-soft);
  }
  .contact-list {
    margin: 22px 0 0;
    padding: 0;
    list-style: none;
  }
  .contact-list .contact-item {
    height: 34px;
    font-size: 21px;
  }
  .contact-icon {
    width: 26px;
    height: 26px;
    margin-right: 10px;
    flex-shrink: 0;
  }
</style>
</head>
<body>
  <div class="business-card">
    <section class="card-front">
      <div class="brand-mark"></div>
      <div class="brand-name">Meridale Nutrition</div>
    </section>
    <div class="card-divider"></div>
    <section class="card-details">
      <div class="details-inner">
        <h1 class="person-name">Dr Daniel Hart</h1>
        <p class="person-title">MBBS, FRACP · Medical Director</p>

        <div class="clinic">
          <p class="clinic-name">WESTMERE CLINIC</p>
          <address class="clinic-address">48 Calder Street, Suite 2, Westmere WA 6011</address>
          <div class="clinic-lines">
            <span class="contact-item">
              <svg class="contact-icon" viewBox="0 0 30 30" aria-hidden="true"><rect width="30" height="30" fill="#2a4766"/><path d="M10 7 L13 7 L14 11 L12 12.5 Q14 17 17.5 18 L19 16 L23 17 L23 20 Q22 23 19 22.5 Q10 20 7.5 11 Q7.5 8 10 7 Z" fill="#2fa9dc"/></svg>
              08 9381 4720
            </span>
            <span class="contact-item">
              <svg class="contact-icon" viewBox="0 0 30 30" aria-hidden="true"><rect width="30" height="30" fill="#2a4766"/><rect x="9" y="6" width="12" height="7" fill="none" stroke="#2fa9dc" stroke-width="1.5"/><rect x="6" y="13" width="18" height="10" fill="none" stroke="#2fa9dc" stroke-width="1.5"/><path d="M10 18 H20" stroke="#2fa9dc" stroke-width="1.5"/></svg>
              08 9381 4721
            </span>
          </div>
        </div>

        <div class="clinic">
          <p class="clinic-name">HARBOURVALE CLINIC</p>
          <address class="clinic-address">112 Linford Road, Level 1, Harbourvale WA 6160</address>
          <div class="clinic-lines">
            <span class="contact-item">
              <svg class="contact-icon" viewBox="0 0 30 30" aria-hidden="true"><rect width="30" height="30" fill="#2a4766"/><path d="M10 7 L13 7 L14 11 L12 12.5 Q14 17 17.5 18 L19 16 L23 17 L23 20 Q22 23 19 22.5 Q10 20 7.5 11 Q7.5 8 10 7 Z" fill="#2fa9dc"/></svg>
              08 9435 2890
            </span>
            <span class="contact-item">
              <svg class="contact-icon" viewBox="0 0 30 30" aria-hidden="true"><rect width="30" height="30" fill="#2a4766"/><rect x="9" y="6" width="12" height="7" fill="none" stroke="#2fa9dc" stroke-width="1.5"/><rect x="6" y="13" width="18" height="10" fill="none" stroke="#2fa9dc" stroke-width="1.5"/><path d="M10 18 H20" stroke="#2fa9dc" stroke-width="1.5"/></svg>
              08 9435 2891
            </span>
          </div>
        </div>

        <ul class="contact-list">
          <li class="contact-item">
            <svg class="contact-icon" viewBox="0 0 30 30" aria-hidden="true"><rect width="30" height="30" fill="#2a4766"/><rect x="6" y="9" width="18" height="12" fill="none" stroke="#2fa9dc" stroke-width="1.6"/><path d="M6 9 L15 16 L24 9 M6 21 L12.5 14.5 M24 21 L17.5 14.5" fill="none" stroke="#2fa9dc" stroke-width="1.6"/></svg>
            clinic@meridalenutrition.com.au
          </li>
          <li class="contact-item">
            <svg class="contact-icon" viewBox="0 0 30 30" aria-hidden="true"><rect width="30" height="30" fill="#2a4766"/><circle cx="15" cy="15" r="8.5" fill="none" stroke="#2fa9dc" stroke-width="1.5"/><ellipse cx="15" cy="15" rx="3.8" ry="8.5" fill="none" stroke="#2fa9dc" stroke-width="1.3"/><path d="M6.5 15 H23.5 M8 10.5 H22 M8 19.5 H22" stroke="#2fa9dc" stroke-width="1.3"/></svg>
            www.meridalenutrition.com.au
          </li>
        </ul>
      </div>
    </section>
  </div>
</body>
</html>
```